Small Business Broker Business Card Design

A business card design for a small business brokerage, which is a financial service, not unlike real estate brokerage, but for small businesses such as laundromats, pizza shops, restaurants, cleaners etc. The designs should all be simple, more conservative in nature, using the colors and font of the logo. Again, think real estate Brokerage as a business context
Contact Information for Business Card
Name: Glen R. Harlow. Title: Small Business Advisor. Email: g.harlow@bayfieldcapitalworks.example. Mobile: (555) 274-3918. Office: (555) 806-2147. www.bayfieldcapitalworks.example

```html
<!DOCTYPE html>
<html lang="en">
<head>
<meta charset="utf-8">
<title>Bayfield Capital Works – Business Card</title>
<link rel="stylesheet" href="https://fonts.googleapis.com/css2?family=Montserrat:wght@400;700;800&family=Arimo:wght@400&display=swap">
<style>
  :root{
    --navy:#132c5e;
    --navy-deep:#0f2450;
    --navy-light:#1b3a73;
    --green:#7cc242;
    --white:#ffffff;
    --stage:#1a1a1c;
  }
  *{box-sizing:border-box;margin:0;padding:0}
  html,body{width:1200px;height:963px;overflow:hidden;background:var(--stage)}
  .stage{width:1200px;height:963px;display:flex;flex-direction:column;align-items:center;justify-content:center;gap:36px}
  .card{width:700px;height:400px;border-radius:22px;background:linear-gradient(135deg,var(--navy-deep),var(--navy) 55%,var(--navy-light));position:relative;overflow:hidden;color:var(--white)}

  /* front */
  .brand{position:absolute;top:86px;left:0;right:0;text-align:center}
  .brand-name{font-family:"Montserrat",sans-serif;font-weight:800;font-size:27px;letter-spacing:2px;text-transform:uppercase;color:var(--white);display:inline-flex;align-items:center;gap:14px}
  .brand-square{width:18px;height:18px;background:var(--green);display:inline-block}
  .tagline{margin-top:10px;font-family:"Montserrat",sans-serif;font-weight:700;font-size:11px;letter-spacing:2.4px;text-transform:uppercase;color:var(--green)}

  .details{position:absolute;left:60px;right:40px;bottom:62px;display:flex;align-items:center}
  .person{width:250px;text-align:right;padding-right:24px}
  .person-name{font-family:"Montserrat",sans-serif;font-weight:800;font-size:22px;letter-spacing:1px;text-transform:uppercase}
  .person-title{font-family:"Arimo",sans-serif;font-size:15px;color:var(--green);margin-top:4px}
  .divider{width:1px;height:112px;background:var(--white);opacity:.85}
  .contacts{list-style:none;padding-left:22px;font-family:"Arimo",sans-serif;font-size:14px;line-height:1.75}
  .contacts li{display:flex;align-items:center;gap:9px}
  .contacts svg{width:13px;height:13px;flex:none}

  /* back */
  .back-texture{position:absolute;inset:0;background:linear-gradient(135deg,#16306a,#1d3f7d 50%,#142b5c)}
  .back-brand{position:absolute;top:50%;left:50%;transform:translate(-50%,-50%);font-family:"Montserrat",sans-serif;font-weight:800;font-size:22px;letter-spacing:2px;text-transform:uppercase;color:var(--white);white-space:nowrap;display:flex;align-items:center;gap:12px}
  .back-brand .brand-square{width:14px;height:14px}
</style>
</head>
<body>
<main class="stage">
  <section class="card card-front">
    <header class="brand">
      <div class="brand-name"><span class="brand-square"></span>Bayfield Capital Works, Inc</div>
      <p class="tagline">Confidently buy or sell a local business today</p>
    </header>
    <div class="details">
      <div class="person">
        <p class="person-name">Glen R. Harlow</p>
        <p class="person-title">Small Business Advisor</p>
      </div>
      <div class="divider"></div>
      <ul class="contacts">
        <li><svg viewBox="0 0 16 16" fill="none" stroke="#7cc242" stroke-width="1.6"><path d="M3 2h3l1.5 3.5-2 1.3a8 8 0 0 0 3.7 3.7l1.3-2L14 10v3a1 1 0 0 1-1 1A11 11 0 0 1 2 3a1 1 0 0 1 1-1z"/></svg>(555) 806-2147</li>
        <li><svg viewBox="0 0 16 16" fill="none" stroke="#7cc242" stroke-width="1.6"><rect x="4" y="1.5" width="8" height="13" rx="1.5"/><path d="M7 12h2"/></svg>(555) 274-3918</li>
        <li><svg viewBox="0 0 16 16" fill="none" stroke="#7cc242" stroke-width="1.6"><rect x="1.5" y="3.5" width="13" height="9" rx="1"/><path d="M1.5 4l6.5 5 6.5-5"/></svg>g.harlow@bayfieldcapitalworks.example</li>
        <li><svg viewBox="0 0 16 16" fill="none" stroke="#7cc242" stroke-width="1.4"><circle cx="8" cy="8" r="6.3"/><ellipse cx="8" cy="8" rx="2.8" ry="6.3"/><path d="M1.7 8h12.6M2.8 4.8h10.4M2.8 11.2h10.4"/></svg>www.bayfieldcapitalworks.example</li>
      </ul>
    </div>
  </section>

  <section class="card card-back">
    <div class="back-texture" role="img" aria-label="Embossed repeating brand pattern in navy tones"></div>
    <div class="back-brand"><span class="brand-square"></span>Bayfield Capital Works</div>
  </section>
</main>
</body>
</html>
```